KLV Plant Services

We are a heavy diesel mechanical business with additional air con certificates, remapping engine rebuilt

Contact Information for Business Card

Company Name, Director Name, Managing Director, Contact details, email and website

Font styles to use
Serif
Script

```html
<!DOCTYPE html>
<html lang="en">
<head>
<meta charset="utf-8">
<title>KLV Plant Services – Business Card</title>
<link rel="stylesheet" href="https://fonts.googleapis.com/css2?family=Open+Sans:wght@400;700&display=swap">
<style>
  :root {
    --backdrop: #d6d6d6;
    --paper: #efefef;
    --navy: #1b1a6b;
    --ink: #1c1c1c;
  }
  * { box-sizing: border-box; margin: 0; padding: 0; }
  html, body {
    width: 1200px;
    height: 1051px;
    overflow: hidden;
    background: var(--backdrop);
    font-family: "Open Sans", Arial, sans-serif;
  }
  .canvas {
    width: 1200px;
    height: 1051px;
    display: flex;
    flex-direction: column;
    align-items: center;
    justify-content: center;
    gap: 70px;
  }
  .card {
    width: 700px;
    height: 400px;
    background: var(--paper);
    border-bottom: 7px solid var(--navy);
    position: relative;
  }
  .card-front {
    display: flex;
    align-items: center;
    justify-content: center;
  }
  .brand {
    display: flex;
    align-items: center;
    gap: 18px;
    color: var(--navy);
    font-weight: 700;
    font-size: 46px;
    letter-spacing: 0.5px;
  }
  .brand-dot {
    width: 38px;
    height: 38px;
    border-radius: 50%;
    background: var(--navy);
  }
  .card-back .identity {
    position: absolute;
    right: 395px;
    top: 120px;
    text-align: right;
    color: var(--navy);
  }
  .identity .name {
    font-weight: 700;
    font-size: 27px;
    letter-spacing: 0.5px;
    line-height: 1.2;
  }
  .identity .role {
    font-size: 19px;
    line-height: 1.3;
  }
  .divider {
    position: absolute;
    left: 330px;
    top: 110px;
    width: 2px;
    height: 125px;
    background: var(--navy);
  }
  .contacts {
    position: absolute;
    left: 352px;
    top: 130px;
    list-style: none;
    color: var(--ink);
    font-size: 20px;
    line-height: 1.45;
  }
  .contacts li {
    display: flex;
    align-items: center;
    gap: 10px;
  }
  .contacts svg {
    width: 15px;
    height: 15px;
    fill: var(--navy);
    flex: none;
  }
  .address {
    position: absolute;
    left: 0;
    right: 0;
    bottom: 60px;
    text-align: center;
    font-size: 20px;
    color: var(--ink);
  }
</style>
</head>
<body>
<main class="canvas">
  <section class="card card-front">
    <div class="brand">
      <span class="brand-dot" aria-hidden="true"></span>
      <span class="brand-name">KLV Plant Services</span>
    </div>
  </section>

  <section class="card card-back">
    <div class="identity">
      <p class="name">DANIEL HART</p>
      <p class="role">Managing Director</p>
    </div>
    <span class="divider" aria-hidden="true"></span>
    <ul class="contacts">
      <li>
        <svg viewBox="0 0 16 16" aria-hidden="true"><path d="M3.5 1 6 4.2 4.6 6a9 9 0 0 0 5.4 5.4L11.8 10 15 12.5 13.2 15C6.5 14.6 1.4 9.5 1 2.8Z"/></svg>
        123 456 789
      </li>
      <li>
        <svg viewBox="0 0 16 16" aria-hidden="true"><path d="M1 3h14v10H1Zm1.5 1.5v.3L8 8.6l5.5-3.8v-.3Zm0 2.1v4.9h11V6.6L8 10.4Z"/></svg>
        info@yourgmail.com
      </li>
      <li>
        <svg viewBox="0 0 16 16" aria-hidden="true"><path d="M8 1a7 7 0 1 0 0 14A7 7 0 0 0 8 1Zm0 1.5c.9 0 1.9 2 2.1 4.7H5.9C6.1 4.5 7.1 2.5 8 2.5ZM2.6 8.8h1.8c.1 1.5.4 2.8.9 3.8a5.5 5.5 0 0 1-2.7-3.8Zm0-1.6a5.5 5.5 0 0 1 2.7-3.8c-.5 1-.8 2.3-.9 3.8Zm5.4 6.3c-.9 0-1.9-2-2.1-4.7h4.2c-.2 2.7-1.2 4.7-2.1 4.7Zm2.7-.9c.5-1 .8-2.3.9-3.8h1.8a5.5 5.5 0 0 1-2.7 3.8Zm.9-5.4c-.1-1.5-.4-2.8-.9-3.8a5.5 5.5 0 0 1 2.7 3.8Z"/></svg>
        www.yourwebsite.com
      </li>
    </ul>
    <p class="address">Your address, City State, Zip 1234</p>
  </section>
</main>
</body>
</html>
```